Building company buisness cards

We are looking for a sharp modern new look for our business cards.We are a New Zealand based company that specialises in house and land packages.We have attached a photo of the current logo and would like to see if it can be improved somehow if needed.We are open to any colours but we have chosen Black and White at this stage. Feel free to change the font and make the logo smarter looking.Play with the colours and see what looks best.We want a card that looks so good know one will want to throw it away!

Target Market(s)

Building profesonals, home buyers

Industry/Entity Type

Building

Contact Information for Business Card

Garrick Tenwood
0275390628
garrickt@hartvale.co.nz

Font styles to use
Serif
Sans Serif

Colors

Designer to choose colors to be used in the design.

Requirements
Must have
• Just the logo on one side and details on the other
• Clean simple looking card
Nice to have
• Round corners and detail like raised or spot UV
• Something that stands out
Should not have
• To title needed, Director etc

```html
<!DOCTYPE html>
<html lang="en">
<head>
<meta charset="utf-8">
<title>Hartvale Business Cards</title>
<link href="https://fonts.googleapis.com/css2?family=Playfair+Display:wght@700;900&family=Arimo:wght@400&display=swap" rel="stylesheet">
<style>
  :root {
    --backdrop: #1b1b1e;
    --card: #1f2022;
    --card-edge: #2a2b2e;
    --gloss: #0b0b0c;
    --silver: #c9cacc;
    --white: #f4f4f4;
    --rule: #d6d6d6;
  }
  * { margin: 0; padding: 0; box-sizing: border-box; }
  html, body { width: 1200px; height: 800px; overflow: hidden; }
  body {
    background: var(--backdrop);
    position: relative;
  }
  .card {
    position: absolute;
    top: 250px;
    width: 520px;
    height: 300px;
    border-radius: 22px;
    background: var(--card);
    box-shadow: 0 0 0 1px var(--card-edge);
    overflow: hidden;
  }
  .card--front { left: 60px; }
  .card--back { left: 620px; }

  .front-mark {
    position: absolute;
    inset: 0;
    display: flex;
    align-items: center;
    justify-content: center;
    gap: 18px;
  }
  .front-mark__name {
    font-family: "Playfair Display", serif;
    font-weight: 900;
    font-size: 62px;
    color: var(--gloss);
    letter-spacing: -0.5px;
  }
  .front-mark__circle {
    width: 58px;
    height: 58px;
    border-radius: 50%;
    border: 2px solid var(--silver);
  }

  .back-ring {
    position: absolute;
    left: 250px;
    top: -40px;
    width: 300px;
    height: 300px;
    border-radius: 50%;
    border: 8px solid var(--silver);
  }
  .details {
    position: absolute;
    left: 34px;
    bottom: 28px;
    width: 240px;
    color: var(--white);
  }
  .details__brand {
    font-family: "Playfair Display", serif;
    font-weight: 900;
    font-size: 46px;
    line-height: 1;
    letter-spacing: -0.5px;
  }
  .details__rule {
    height: 1px;
    background: var(--rule);
    margin: 10px 0 8px;
  }
  .details__name {
    font-family: "Playfair Display", serif;
    font-weight: 700;
    font-size: 17px;
  }
  .details__list {
    list-style: none;
    font-family: "Arimo", sans-serif;
    font-size: 14px;
  }
  .details__item {
    display: flex;
    align-items: center;
    gap: 8px;
    margin-top: 5px;
  }
  .details__icon { width: 16px; height: 16px; flex: none; }
</style>
</head>
<body>
  <section class="card card--front" aria-label="Card front">
    <div class="front-mark">
      <span class="front-mark__name">Hartvale</span>
      <span class="front-mark__circle"></span>
    </div>
  </section>

  <section class="card card--back" aria-label="Card back">
    <div class="back-ring"></div>
    <div class="details">
      <div class="details__brand">Hartvale</div>
      <div class="details__rule"></div>
      <div class="details__name">Garrick Tenwood</div>
      <div class="details__rule"></div>
      <ul class="details__list">
        <li class="details__item">
          <svg class="details__icon" viewBox="0 0 16 16" aria-hidden="true">
            <circle cx="8" cy="8" r="7.2" fill="none" stroke="#f4f4f4" stroke-width="1"/>
            <rect x="5.5" y="4" width="5" height="8" rx="1" fill="none" stroke="#f4f4f4" stroke-width="1"/>
          </svg>
          <span>0275390628</span>
        </li>
        <li class="details__item">
          <svg class="details__icon" viewBox="0 0 16 16" aria-hidden="true">
            <circle cx="8" cy="8" r="7.2" fill="none" stroke="#f4f4f4" stroke-width="1"/>
            <rect x="4" y="5.2" width="8" height="5.6" fill="none" stroke="#f4f4f4" stroke-width="1"/>
            <path d="M4 5.2 L8 8.6 L12 5.2" fill="none" stroke="#f4f4f4" stroke-width="1"/>
          </svg>
          <span>garrickt@hartvale.co.nz</span>
        </li>
      </ul>
    </div>
  </section>
</body>
</html>
```